RW Framewell Inc Business cards

We need business cards using our existing logo but slightly modified. Right now the logo says RW Loadbearing Masonry. We want to keep the RW part of the design, but replace the Structural Concrete portion with "FRAMEWELL". Please see the attached file.
Ideally this would be a blank template so we can add Different Names, titles, and phone numbers later.
On the one side we want only the logo and on the other side the detail. I'm attaching an example for you to see.
Please reach out with any other questions. Our address and other details will be given out once we find a design we like.

Target Market(s)

Construction Industry

```html
<!DOCTYPE html>
<html lang="en">
<head>
<meta charset="utf-8">
<title>RW Framewell Inc – Business Cards</title>
<link rel="stylesheet" href="https://fonts.googleapis.com/css2?family=Michroma&family=Open+Sans:wght@400&display=swap">
<style>
  :root {
    --backdrop: #d9c6a6;
    --card-white: #ffffff;
    --brand-blue: #1b73c3;
    --text-grey: #6b6b6b;
    --icon-blue: #1b73c3;
    --on-blue: #ffffff;
  }
  * { box-sizing: border-box; margin: 0; padding: 0; }
  html, body {
    width: 1200px; height: 859px; overflow: hidden;
    background: var(--backdrop);
  }
  .canvas { position: relative; width: 1200px; height: 859px; }
  .card {
    position: absolute; top: 289px; width: 502px; height: 285px;
    box-shadow: 0 10px 24px rgba(60, 40, 15, 0.35);
  }
  .card--front { left: 59px; background: var(--card-white); }
  .card--back { left: 639px; background: var(--brand-blue); }

  .wordmark {
    position: absolute;
    font-family: "Michroma", sans-serif;
    font-size: 22px; letter-spacing: 1px; white-space: nowrap;
    line-height: 1;
  }
  .card--front .wordmark { left: 19px; top: 28px; color: var(--brand-blue); }
  .card--back .wordmark { right: 24px; top: 148px; color: var(--on-blue); }

  .holder { position: absolute; left: 19px; top: 143px; }
  .holder__name {
    font-family: "Michroma", sans-serif; font-size: 18px;
    color: var(--brand-blue); letter-spacing: 0.5px; word-spacing: 6px;
  }
  .holder__title {
    font-family: "Open Sans", sans-serif; font-size: 13.5px;
    color: var(--text-grey); margin-top: 1px;
  }

  .contacts { position: absolute; left: 19px; top: 202px; list-style: none; }
  .contacts li {
    display: flex; align-items: center; gap: 6px; height: 17px;
    font-family: "Open Sans", sans-serif; font-size: 13px; color: var(--text-grey);
  }
  .contacts svg { width: 12px; height: 12px; fill: var(--icon-blue); flex: none; }

  .address {
    position: absolute; right: 19px; top: 236px; text-align: right;
    font-family: "Open Sans", sans-serif; font-size: 13px;
    color: var(--text-grey); line-height: 17px; font-style: normal;
  }
  .back-url {
    position: absolute; left: 17px; bottom: 15px;
    font-family: "Open Sans", sans-serif; font-size: 13px; color: var(--on-blue);
  }
</style>
</head>
<body>
<main class="canvas">
  <section class="card card--front" aria-label="Business card, detail side">
    <div class="wordmark">RW FRAMEWELL</div>
    <div class="holder">
      <p class="holder__name">ALEX MORGAN</p>
      <p class="holder__title">Chief Officer</p>
    </div>
    <ul class="contacts">
      <li><svg viewBox="0 0 24 24" aria-hidden="true"><path d="M6.6 10.8a15 15 0 0 0 6.6 6.6l2.2-2.2a1 1 0 0 1 1-.25 11.4 11.4 0 0 0 3.6.57 1 1 0 0 1 1 1V20a1 1 0 0 1-1 1A17 17 0 0 1 3 4a1 1 0 0 1 1-1h3.5a1 1 0 0 1 1 1c0 1.25.2 2.45.57 3.57a1 1 0 0 1-.25 1z"/></svg>+00 8 38 00 00</li>
      <li><svg viewBox="0 0 24 24" aria-hidden="true"><path d="M7 1h10a2 2 0 0 1 2 2v18a2 2 0 0 1-2 2H7a2 2 0 0 1-2-2V3a2 2 0 0 1 2-2zm0 3v14h10V4zm5 15.5a1.2 1.2 0 1 0 0 2.4 1.2 1.2 0 0 0 0-2.4z"/></svg>+00 0 90 00 00</li>
      <li><svg viewBox="0 0 24 24" aria-hidden="true"><path d="M2 5h20v14H2zm2 2v.5l8 5.5 8-5.5V7zm0 3v7h16v-7l-8 5.5z"/></svg>info@rwframewell.com</li>
      <li><svg viewBox="0 0 24 24" aria-hidden="true"><path d="M12 2a10 10 0 1 0 0 20 10 10 0 0 0 0-20zm6.9 9h-3a15 15 0 0 0-1.3-6.2A8 8 0 0 1 18.9 11zM12 4.1c.9 1.3 1.8 3.8 1.9 6.9h-3.8c.1-3.1 1-5.6 1.9-6.9zM9.4 4.8A15 15 0 0 0 8.1 11h-3a8 8 0 0 1 4.3-6.2zM5.1 13h3a15 15 0 0 0 1.3 6.2A8 8 0 0 1 5.1 13zm6.9 6.9c-.9-1.3-1.8-3.8-1.9-6.9h3.8c-.1 3.1-1 5.6-1.9 6.9zm2.6-.7a15 15 0 0 0 1.3-6.2h3a8 8 0 0 1-4.3 6.2z"/></svg>www.rwframewell.com</li>
    </ul>
    <address class="address">Your address line here<br>Country/ State</address>
  </section>

  <section class="card card--back" aria-label="Business card, logo side">
    <div class="wordmark">RW FRAMEWELL</div>
    <p class="back-url">www.rwframewell.com</p>
  </section>
</main>
</body>
</html>
```